Road Construction Company needs business cards

We would like a new business card designed for our business.

We're a road construction company based in Qld, Australia.

Can the business card please have the following information on it.

Name: Warren Halbeck
Position: General Manager
Phone: 0472 915 348
Email: Warren.halbeck@tovrin.com.au
Address: 87 Marrow Ave, Pendlebay, QLD, 4023
Website: www.tovrin.com.au

Visually we'd like the card to be professional and simple.

Attached is our logo.

Our website is www.tovrin.com.au

Target Market(s)

Men aged 25-60

Contact Information for Business Card

As listed in project description

Font styles to use
Serif

Requirements
Must have
• Large logo on back of card

```html
<!DOCTYPE html>
<html lang="en">
<head>
<meta charset="utf-8">
<title>Tovrin – Business Card</title>
<link rel="stylesheet" href="https://fonts.googleapis.com/css2?family=Open+Sans:wght@400;600;700;800&display=swap">
<style>
  :root {
    --backdrop: #232323;
    --brand-blue: #1356a6;
    --sky-blue: #42a8d8;
    --card-white: #ffffff;
    --logo-dark: #0c1624;
    --text-light: #ffffff;
  }
  * { box-sizing: border-box; margin: 0; padding: 0; }
  html, body {
    width: 1200px; height: 780px; overflow: hidden;
    background: var(--backdrop);
    font-family: "Open Sans", Arial, sans-serif;
  }
  .canvas {
    position: relative; width: 1200px; height: 780px;
    display: flex; align-items: center; justify-content: center; gap: 40px;
  }
  .card {
    position: relative; width: 540px; height: 310px;
    border-radius: 22px; overflow: hidden;
  }
  /* Back of card */
  .card--back {
    background: var(--brand-blue);
    display: flex; align-items: center; justify-content: center;
  }
  .wordmark {
    font-weight: 800; letter-spacing: 0.02em; text-transform: uppercase;
    line-height: 1;
  }
  .card--back .wordmark { font-size: 72px; color: var(--logo-dark); }

  /* Front of card */
  .card--front { background: var(--card-white); }
  .wave { position: absolute; inset: 0; width: 100%; height: 100%; }
  .card--front .wordmark {
    position: absolute; left: 34px; top: 44px;
    font-size: 40px; color: var(--brand-blue);
  }
  .contact {
    position: absolute; right: 26px; top: 96px;
    text-align: right; color: var(--text-light);
  }
  .contact__name {
    font-size: 21px; font-weight: 700; text-transform: uppercase;
    letter-spacing: 0.01em; line-height: 1.1;
  }
  .contact__role { font-size: 13px; font-weight: 600; margin-bottom: 10px; }
  .contact__address { font-size: 12.5px; line-height: 1.35; margin-bottom: 10px; }
  .contact__line {
    display: flex; justify-content: flex-end; align-items: center; gap: 6px;
    font-size: 12.5px; line-height: 1.55;
  }
  .contact__icon { width: 12px; height: 12px; flex: none; }
</style>
</head>
<body>
  <main class="canvas">
    <section class="card card--back" aria-label="Business card back">
      <div class="wordmark">Tovrin</div>
    </section>

    <section class="card card--front" aria-label="Business card front">
      <svg class="wave" viewBox="0 0 540 310" preserveAspectRatio="none" aria-hidden="true">
        <defs>
          <path id="swoosh" d="M380 0 C310 50 280 150 215 205 C160 248 90 256 0 264 L0 340 L580 340 L580 0 Z"/>
        </defs>
        <use href="#swoosh" transform="translate(-34 -26)" fill="var(--brand-blue)"/>
        <use href="#swoosh" transform="translate(-26 -19)" fill="var(--card-white)"/>
        <use href="#swoosh" transform="translate(-22 -15)" fill="var(--sky-blue)"/>
        <use href="#swoosh" transform="translate(-8 -6)" fill="var(--card-white)"/>
        <use href="#swoosh" transform="translate(0 0)" fill="var(--brand-blue)"/>
      </svg>

      <div class="wordmark">Tovrin</div>

      <div class="contact">
        <p class="contact__name">Warren Halbeck</p>
        <p class="contact__role">General Manager</p>
        <p class="contact__address">87 Marrow Ave,<br>Pendlebay, QLD, 4023</p>
        <p class="contact__line">0472 915 348
          <svg class="contact__icon" viewBox="0 0 12 12" aria-hidden="true"><path fill="#fff" d="M2.5 1 L4.5 1 L5 3.5 L3.8 4.5 C4.4 5.9 5.9 7.4 7.5 8.1 L8.5 7 L11 7.5 L11 9.5 C11 10.3 10.3 11 9.5 11 C5 11 1 7 1 2.5 C1 1.7 1.7 1 2.5 1 Z"/></svg>
        </p>
        <p class="contact__line">www.tovrin.com.au
          <svg class="contact__icon" viewBox="0 0 12 12" aria-hidden="true"><circle cx="6" cy="6" r="5" fill="none" stroke="#fff" stroke-width="1.2"/><ellipse cx="6" cy="6" rx="2" ry="5" fill="none" stroke="#fff" stroke-width="1"/><path d="M1 6 H11" stroke="#fff" stroke-width="1"/></svg>
        </p>
        <p class="contact__line">Warren.halbeck@tovrin.com.au
          <svg class="contact__icon" viewBox="0 0 12 12" aria-hidden="true"><rect x="1" y="2.5" width="10" height="7" rx="1" fill="none" stroke="#fff" stroke-width="1.2"/><path d="M1.5 3 L6 6.5 L10.5 3" fill="none" stroke="#fff" stroke-width="1.2"/></svg>
        </p>
      </div>
    </section>
  </main>
</body>
</html>
```